Business Cards for a law firm

Business cards for our law firm. Use our silhoette logo and OAK PARTNERS - check our website (www.oakpartners.example)

Contact Information for Business Card

our silhouette logo, OAK PARTNERS, 800-555-0147, Dorian Pemberton, dorian@oakpartners.example

Requirements
Must have
• our silhouette logo, OAK PARTNERS, 800-555-0147, Dorian Pemberton, dorian@oakpartners.example

```html
<!DOCTYPE html>
<html lang="en">
<head>
<meta charset="utf-8">
<title>Oak Partners Business Cards</title>
<link rel="stylesheet" href="https://fonts.googleapis.com/css2?family=Share+Tech&display=swap">
<style>
  :root {
    --backdrop: #e4e4e4;
    --card: #ffffff;
    --brand-blue: #0b16a3;
    --ink: #111111;
  }
  * { margin: 0; padding: 0; box-sizing: border-box; }
  html, body { width: 1200px; height: 1200px; overflow: hidden; background: var(--backdrop); }
  body { position: relative; font-family: "Share Tech", sans-serif; }
  .card { position: absolute; left: 222px; width: 756px; height: 432px; background: var(--card); }
  .card-front { top: 154px; }
  .card-back { top: 614px; }
  .name-rule { position: absolute; left: 0; top: 223px; width: 419px; height: 3px; background: var(--brand-blue); }
  .holder-name {
    position: absolute; left: 430px; top: 196px;
    font-size: 44px; line-height: 1; color: var(--brand-blue); white-space: nowrap;
    transform: scaleX(0.9); transform-origin: left center;
  }
  .contact-item { position: absolute; top: 301px; width: 260px; margin-left: -130px; text-align: center; }
  .contact-phone { left: 140px; }
  .contact-mail { left: 348px; }
  .contact-place { left: 587px; }
  .contact-icon { display: block; width: 38px; height: 38px; margin: 0 auto 12px; }
  .contact-text { font-size: 17px; line-height: 18px; color: var(--ink); white-space: nowrap; letter-spacing: 0.3px; }
  .brand-lockup { position: absolute; left: 107px; top: 157px; display: flex; align-items: center; gap: 18px; }
  .brand-square { width: 78px; height: 78px; background: var(--brand-blue); }
  .brand-name { font-size: 62px; line-height: 1; color: var(--brand-blue); letter-spacing: 2px; white-space: nowrap; }
</style>
</head>
<body>
  <section class="card card-front">
    <div class="name-rule"></div>
    <h1 class="holder-name">Dorian Pemberton</h1>

    <div class="contact-item contact-phone">
      <svg class="contact-icon" viewBox="0 0 38 38" aria-hidden="true">
        <rect width="38" height="38" rx="7" fill="var(--brand-blue)"/>
        <path d="M12 9c1.5-.8 2.5 0 3.2 1.6l1 2.4c.4 1-.2 1.8-1 2.4l-.8.6c.9 2.6 2.8 4.6 5.4 5.6l.6-.8c.6-.8 1.4-1.3 2.4-.9l2.4 1c1.6.7 2.4 1.7 1.6 3.2l-.6 1.4c-.8 1.5-2.6 1.8-4.6 1.1C14.6 24.9 11.1 21.4 9.4 15.4 8.8 13.4 9 11.8 10.6 10z" fill="#ffffff"/>
      </svg>
      <p class="contact-text">800-555-0147<br>000000000000</p>
    </div>

    <div class="contact-item contact-mail">
      <svg class="contact-icon" viewBox="0 0 38 38" aria-hidden="true">
        <rect width="38" height="38" rx="7" fill="var(--brand-blue)"/>
        <rect x="8" y="11" width="22" height="16" rx="2.5" fill="#ffffff"/>
        <path d="M8.5 12l10.5 9 10.5-9" fill="none" stroke="var(--brand-blue)" stroke-width="1.6"/>
      </svg>
      <p class="contact-text">dorian@oakpartners.example<br>Www.yourweb.com</p>
    </div>

    <div class="contact-item contact-place">
      <svg class="contact-icon" viewBox="0 0 38 38" aria-hidden="true">
        <rect width="38" height="38" rx="7" fill="var(--brand-blue)"/>
        <path d="M19 8a7 7 0 0 1 7 7c0 4-4 9.5-7 14-3-4.5-7-10-7-14a7 7 0 0 1 7-7z" fill="#ffffff"/>
        <circle cx="19" cy="15" r="2.8" fill="var(--brand-blue)"/>
      </svg>
      <p class="contact-text">Your Street,City,State,<br>Pin Code,Country</p>
    </div>
  </section>

  <section class="card card-back">
    <div class="brand-lockup">
      <div class="brand-square"></div>
      <h2 class="brand-name">OAK PARTNERS</h2>
    </div>
  </section>
</body>
</html>
```